Kelmo website design on shopify

Job Description:
As a web designer for Kelmo, you will be the driving force behind designing and developing our new e-commerce website. Your responsibility will be to create an attractive, functional, and intuitive online shopping experience where customers can effortlessly discover and purchase high-quality supplements such as pre-workout, creatine, and protein shakes. Your design will play a crucial role in enhancing our brand and engaging our target audience.

```html
<!DOCTYPE html>
<html lang="en">
<head>
<meta charset="utf-8">
<title>Kelmo — Fueling Health Not Expenses</title>
<link href="https://fonts.googleapis.com/css2?family=Roboto:wght@400;500;700;900&display=swap" rel="stylesheet">
<style>
:root{
  --purple:#6e2a8c;
  --purple-dark:#5a1f74;
  --ink:#1a1a1a;
  --text:#333;
  --muted:#555;
  --line:#e2e2e2;
  --footer:#222222;
  --footer-text:#e8e8e8;
  --white:#fff;
}
*{margin:0;padding:0;box-sizing:border-box}
html,body{width:1200px;height:3637px;overflow:hidden}
body{position:relative;font-family:'Roboto',Arial,sans-serif;color:var(--text);background:var(--white)}
.abs{position:absolute}
a{color:inherit;text-decoration:none}

.promo-bar{left:0;top:0;width:1200px;height:34px;background:var(--purple);color:#fff;font-size:12px;text-align:center;line-height:34px}
.site-header{left:0;top:34px;width:1200px;height:79px;background:#fff;border-bottom:1px solid var(--line)}
.brand{left:113px;top:20px;display:flex;align-items:center;gap:10px}
.brand-mark{width:30px;height:30px;border-radius:50%;background:var(--purple)}
.brand-name{font-size:30px;font-weight:500;color:var(--purple);letter-spacing:1px}
.main-nav{left:535px;top:30px;display:flex;gap:28px;font-size:14px;color:#222}
.header-icons{left:998px;top:28px;display:flex;gap:16px}

.hero{left:0;top:113px;width:1200px;height:593px;background:linear-gradient(110deg,#8a8177 0%,#b2aba2 30%,#d8d1c6 55%,#7a5a45 80%,#4d3a2c 100%)}
.hero-eyebrow{left:108px;top:272px;font-size:27px;font-weight:700;color:#fff}
.hero-title{left:104px;top:310px;font-size:124px;font-weight:900;color:#fff;line-height:1;letter-spacing:-2px}
.hero-tagline{left:107px;top:437px;font-size:33px;font-weight:700;color:#fff}
.btn-primary{left:109px;top:501px;width:151px;height:43px;background:var(--purple);color:#fff;font-size:13px;font-weight:700;display:flex;align-items:center;justify-content:center;gap:10px}

.section-title{left:0;width:1200px;text-align:center;font-size:31px;font-weight:700;color:var(--ink)}

.product-card{width:236px}
.product-media{position:relative;width:236px;height:201px;border:1px solid var(--line);background:#fff;overflow:hidden}
.product-photo{position:absolute;left:50%;top:22px;transform:translateX(-50%);width:90px;height:150px;border-radius:14px;background:linear-gradient(90deg,#d9d9d9,#fafafa 45%,#cfcfcf)}
.badge-sale{position:absolute;left:6px;bottom:6px;background:var(--purple);color:#fff;font-size:13px;padding:2px 10px;border-radius:12px}
.product-name{margin-top:15px;text-align:center;font-size:17px;font-weight:700;color:var(--ink)}
.product-price{margin-top:7px;text-align:center;font-size:15px;font-weight:500;color:#444}

.category-photo{background:linear-gradient(135deg,#8a8c92,#c9c6c2 50%,#6d5a4a)}
.category-link{font-size:13px;font-weight:700;color:var(--ink);display:flex;align-items:center;gap:7px}

.video-block{left:112px;top:2310px;width:976px;height:507px;background:linear-gradient(120deg,#d8d5cf,#b9b2a8 50%,#8a7b6a)}
.play-btn{left:574px;top:2548px}

.testimonial{width:440px;text-align:center}
.stars{color:var(--purple);font-size:16px;letter-spacing:3px}
.quote{margin-top:10px;font-size:16.5px;line-height:25.5px;color:#444}
.author{margin-top:10px;font-size:16px;font-weight:700;color:var(--purple)}
.arrow{font-size:28px;color:#111}

.site-footer{left:0;top:3151px;width:1200px;height:486px;background:var(--footer);color:var(--footer-text)}
.footer-heading{font-size:18px;font-weight:700;color:#fff}
.footer-links{list-style:none;margin-top:13px}
.footer-links li{font-size:15.5px;line-height:30px}
.mission{width:430px;font-size:14.5px;line-height:25px;text-align:justify;margin-top:15px}
.email-field{left:114px;top:3480px;width:390px;height:43px;background:#fff;display:flex;align-items:center;justify-content:space-between;padding:0 18px;font-size:14px;color:#666}
.socials{left:918px;top:3484px;display:flex;gap:8px}
.social{height:34px;padding:0 9px;border:1px solid #ddd;border-radius:17px;font-size:11px;line-height:32px;color:#fff}
.footer-divider{left:113px;top:3562px;width:978px;height:1px;background:#3a3a3a}
.payments{left:113px;top:3582px;display:flex;gap:14px;font-size:15px;font-weight:700;color:#8f7fc4}
.copyright{left:760px;top:3585px;width:326px;text-align:right;font-size:13.5px;color:#fff}
</style>
</head>
<body>

<div class="abs promo-bar">Free shipping available on all orders!</div>

<header class="abs site-header">
  <div class="abs brand"><span class="brand-mark"></span><span class="brand-name">KELMO</span></div>
  <nav class="abs main-nav">
    <a href="#">HOME</a><a href="#">ABOUT</a><a href="#">SHOP</a><a href="#">TESTIMONIALS</a><a href="#">CONATCT US</a>
  </nav>
  <div class="abs header-icons">
    <svg width="18" height="18" viewBox="0 0 18 18"><circle cx="7.5" cy="7.5" r="5.5" fill="none" stroke="#6e2a8c" stroke-width="2.4"/><line x1="11.5" y1="11.5" x2="16" y2="16" stroke="#6e2a8c" stroke-width="2.6"/></svg>
    <svg width="18" height="18" viewBox="0 0 18 18"><circle cx="9" cy="5" r="4" fill="#6e2a8c"/><path d="M2 17c0-5 3-7 7-7s7 2 7 7z" fill="#6e2a8c"/></svg>
    <svg width="20" height="18" viewBox="0 0 20 18"><path d="M1 2h3l2 9h10l2-7H5" fill="none" stroke="#6e2a8c" stroke-width="2.2"/><circle cx="8" cy="15" r="1.8" fill="#6e2a8c"/><circle cx="15" cy="15" r="1.8" fill="#6e2a8c"/></svg>
  </div>
</header>

<section class="abs hero" role="img" aria-label="Smiling woman at a kitchen table holding a supplement bottle, with fruit bowl and breakfast"></section>
<div class="abs hero-eyebrow">WELCOME TO</div>
<div class="abs hero-title">KELMO</div>
<div class="abs hero-tagline">Fueling Health Not Expenses</div>
<a class="abs btn-primary" href="#">GET STARTED
  <svg width="13" height="13" viewBox="0 0 13 13"><circle cx="6.5" cy="6.5" r="6.5" fill="#fff"/><path d="M5 3.5l3 3-3 3" fill="none" stroke="#6e2a8c" stroke-width="1.8"/></svg>
</a>

<h2 class="abs section-title" style="top:786px">OUR PRODUCTS</h2>

<div class="abs product-card" style="left:109px;top:861px"><div class="product-media"><div class="product-photo" role="img" aria-label="White supplement jar"></div><span class="badge-sale">Sale</span></div><div class="product-name">Products Tittle</div><div class="product-price">From $22.95</div></div>
<div class="abs product-card" style="left:357px;top:861px"><div class="product-media"><div class="product-photo" role="img" aria-label="Round metal tin" style="width:140px;height:80px;top:50px;border-radius:40px"></div><span class="badge-sale">Sale</span></div><div class="product-name">Products Tittle</div><div class="product-price">From $22.95</div></div>
<div class="abs product-card" style="left:607px;top:861px"><div class="product-media"><div class="product-photo" role="img" aria-label="White supplement bottle" style="width:80px"></div></div><div class="product-name">Products Tittle</div><div class="product-price">From $22.95</div></div>
<div class="abs product-card" style="left:855px;top:861px"><div class="product-media"><div class="product-photo" role="img" aria-label="Open white capsule bottle" style="width:80px;top:10px;height:170px"></div><span class="badge-sale">Sale</span></div><div class="product-name">Products Tittle</div><div class="product-price">From $22.95</div></div>

<div class="abs product-card" style="left:109px;top:1163px"><div class="product-media"><div class="product-photo" role="img" aria-label="Blue shaker bottle with protein powder" style="background:linear-gradient(90deg,#1aa7d6,#6fd2f0 50%,#1790bb)"></div></div><div class="product-name">Products Tittle</div><div class="product-price">From $22.95</div></div>
<div class="abs product-card" style="left:357px;top:1163px"><div class="product-media"><div class="product-photo" role="img" aria-label="Clear jar of protein powder" style="background:linear-gradient(90deg,#c9b3a6,#efe4dc 50%,#c2a698)"></div></div><div class="product-name">Products Tittle</div><div class="product-price">From $22.95</div></div>
<div class="abs product-card" style="left:607px;top:1163px"><div class="product-media"><div class="product-photo" role="img" aria-label="Red-lid jar of powder with bowl of supplements" style="background:linear-gradient(180deg,#c8353a 0 18%,#d7b8a7 18%,#e9d8cc)"></div><span class="badge-sale">Sale</span></div><div class="product-name">Products Tittle</div><div class="product-price">From $22.95</div></div>
<div class="abs product-card" style="left:855px;top:1163px"><div class="product-media"><div class="product-photo" role="img" aria-label="White tub with black lid" style="width:110px;height:120px;top:38px;background:linear-gradient(180deg,#1a1a1a 0 18%,#f1f1f1 18%,#dcdcdc)"></div><span class="badge-sale">Sale</span></div><div class="product-name">Products Tittle</div><div class="product-price">From $22.95</div></div>

<h2 class="abs section-title" style="top:1500px">HIGH-QUALITY SUPPLEMENTS</h2>

<div class="abs category-photo" style="left:114px;top:1574px;width:550px;height:610px" role="img" aria-label="Man scooping creatine powder into a shaker"></div>
<a class="abs category-link" href="#" style="left:116px;top:2210px">CREATINE <svg width="12" height="12" viewBox="0 0 12 12"><circle cx="6" cy="6" r="6" fill="#1a1a1a"/><path d="M4.5 3l3 3-3 3" fill="none" stroke="#fff" stroke-width="1.6"/></svg></a>

<div class="abs category-photo" style="left:679px;top:1574px;width:407px;height:277px;background:linear-gradient(135deg,#5f6a3c,#c8a36a 55%,#f2c27a)" role="img" aria-label="Woman stretching outdoors at sunset before a workout"></div>
<a class="abs category-link" href="#" style="left:680px;top:1873px">PRE-WORKOUT <svg width="12" height="12" viewBox="0 0 12 12"><circle cx="6" cy="6" r="6" fill="#1a1a1a"/><path d="M4.5 3l3 3-3 3" fill="none" stroke="#fff" stroke-width="1.6"/></svg></a>

<div class="abs category-photo" style="left:679px;top:1910px;width:407px;height:277px;background:linear-gradient(135deg,#b89a84,#ece6dc 45%,#6b6b6b)" role="img" aria-label="Glasses of protein shakes with powder and dumbbells"></div>
<a class="abs category-link" href="#" style="left:679px;top:2208px">PROTEIN SHAKES <svg width="12" height="12" viewBox="0 0 12 12"><circle cx="6" cy="6" r="6" fill="#1a1a1a"/><path d="M4.5 3l3 3-3 3" fill="none" stroke="#fff" stroke-width="1.6"/></svg></a>

<div class="abs video-block" role="img" aria-label="Video: woman mixing a protein shake in a bright kitchen with fruit"></div>
<svg class="abs play-btn" width="52" height="52" viewBox="0 0 52 52"><circle cx="26" cy="26" r="26" fill="#fff"/><circle cx="26" cy="26" r="22" fill="#6e2a8c"/><path d="M21 17l14 9-14 9z" fill="#fff"/></svg>

<div class="abs testimonial" style="left:122px;top:2905px">
  <div class="stars">★★★★★</div>
  <p class="quote">Lorem ipsum dolor sit amet consectetur adipiscing elit sed do eiusmod tempor incididunt ut labore et dolore magna aliquad enim ad minim veniam, quis nostrud exercitation ullamco. laboris nisi ut ali</p>
  <div class="author">Jhon Doe</div>
</div>
<div class="abs testimonial" style="left:637px;top:2905px">
  <div class="stars">★★★★★</div>
  <p class="quote">Lorem ipsum dolor sit amet consectetur adipiscing elit sed do eiusmod tempor incididunt ut labore et dolore magna aliqua. Ut enim ad minim veniam, quis nostrud exercitation ullamco. laboris nisi ut ali</p>
  <div class="author">Jhon Doe</div>
</div>
<svg class="abs" style="left:62px;top:2976px" width="14" height="22" viewBox="0 0 14 22"><path d="M11 2L3 11l8 9" fill="none" stroke="#111" stroke-width="2.4"/></svg>
<svg class="abs" style="left:1122px;top:2976px" width="14" height="22" viewBox="0 0 14 22"><path d="M3 2l8 9-8 9" fill="none" stroke="#111" stroke-width="2.4"/></svg>

<footer class="abs site-footer"></footer>
<div class="abs" style="left:113px;top:3209px">
  <h3 class="footer-heading">QUICK LINKS</h3>
  <ul class="footer-links"><li>Home</li><li>About</li><li>Shop</li><li>Testimonials</li><li>Conatct Us</li></ul>
</div>
<div class="abs" style="left:397px;top:3209px">
  <h3 class="footer-heading">OTHER LINKS</h3>
  <ul class="footer-links"><li>About us</li><li>Military Discount</li><li>Terms &amp; Conditions</li><li>Privacy Policy</li></ul>
</div>
<div class="abs" style="left:654px;top:3209px">
  <h3 class="footer-heading">OUR MISSION</h3>
  <p class="mission">Lorem ipsum dolor sit amet, consectetur adipiscing elit, sed do eiusmod tempor incididunt ut labore et dolore magna aliqua. Ut enim ad minim veniam, quis nostrud exercitation ullamco laboris nisi ut aliquip ex ea commodo consequat. Duis aute irure dolor in reprehenderit in voluptate velit esse cillum dolore eu fugi</p>
</div>
<h3 class="abs footer-heading" style="left:113px;top:3442px">SUBSCRIBE TO OUR EMAILS</h3>
<div class="abs email-field"><span>Email Address</span><span style="color:#222;font-size:18px">→</span></div>
<div class="abs socials">
  <span class="social">Lumo</span><span class="social">Chirra</span><span class="social">Pixa</span><span class="social">Linqo</span>
</div>
<div class="abs footer-divider"></div>
<div class="abs payments"><span>Cardora</span><span>Orbix</span><span>Amvale</span><span>Paylio</span></div>
<div class="abs copyright">© 2023 Kelmo &nbsp;|&nbsp; All Rights Reserved |</div>

</body>
</html>
```